Attraktives Etiketten-Design für Honig
Zielgruppe
Wir sind eine kleine verdanta-zertifizierte Imkerei und suchen ein attraktives Ettiket für unsere erstklassigen Honige. Unsere Zielgruppe sind Menschen mit einem nachhaltig, ökologischen Bewusstsein.
Aufgabenstellung
Wir verkaufen zur Zeit vor allem Waldhonig, streben aber auch einen Blütenhonig an. Das Etikett soll daher entweder den Wald wiederspiegeln oder aber neutral sein, so dass der Schriftzug Waldhonig oder Blütenhonig jeweils eingesetzt werden kann. Wichtig ist mir der Ortszusatz 'aus dem Glottertal'.
Ein Etikett, das mir sehr gut gefällt, ist das von der Imkerei Walko (http://imkereiwalko-beispiel.de/honig/). Toll wäre, wenn solche Goldelemente Eingang ins Etikett fänden. Das Verspielte finde ich auch schön. Es kann aber auch ganz gradlienig sein. Nur nicht halb-halb. Im Anhang habe ich auch das Bild einer Blumenbiene. Dieses Bild kann verwendet werden, muss aber nicht sein.
Unser Glas ist ein 400g Rundglas. (https://www.behaelterwelt-beispiel.de/gh/Sturzglas-350-ml--41.html)
Etikettengröße 133 x 60 mm, aber da sind wir offen für andere Maße.
Folgende Angaben sollen auf dem Etikett prominent erscheinen:
- Waldhonig bzw. Blütenhonig
- aus dem Glottertal
Folgende Angaben sind auserdem notwendig:
- Da wir verdanta-zertifiziert sind, muss oben am Rand mittig das verdanta-Label angebracht werden.
- EU-Bio-Logo mit folgender Beschriftung:
* DE-Öko-087
* Deutsche Landwirtschaft
* Verdanta-Betrieb 53184
- (Inhalt) 400g
- Deutscher Bienenhonig
- Imkerei tamlin: Mattias Grunbeck, Kesselweg 48b, 79412 Glottertal, 07684/551037, www.tamlinhonig-beispiel.de
- Mindestens haltbar bis: L 30. l Okt. Nov. Dez. l 2022 2023 2024 2025
Die Angaben beim Mindesthaltbarkeitsdatum muss ich über die Jahre anpassen können.
Auch das Feld 'aus dem Glottertal' sollte ich durch einen anderen Ortsnamen ersetzen können.
Der Infotext bei dem Etikett im Anhang kommt vermutlich auf ein Extraetikett an die Rückseite.
Die Homepage befindet sich derzeit noch im Aufbau.

```html
<!DOCTYPE html>
<html lang="de">
<head>
<meta charset="utf-8">
<title>Waldhonig Etikett</title>
<link rel="stylesheet" href="https://fonts.googleapis.com/css2?family=Great+Vibes&family=Dancing+Script:wght@500&family=Open+Sans+Condensed:wght@500&family=Open+Sans:wght@600&display=swap">
<style>
  :root {
    --page: #ffffff;
    --gold-light: #efe7a6;
    --gold-mid: #a88a3a;
    --gold-deep: #8f7430;
    --gold-pale: #f2edcc;
    --script-green: #4f8f2a;
    --swash-green: #5c9a2c;
    --ink: #2a2417;
    --brand-orange: #ee7b1f;
    --forest-dark: #2f5a1a;
    --forest-mid: #4c7a22;
    --forest-light: #6f9d2d;
    --tag-cream: #efe8b0;
    --tag-ink: #2b2a20;
    --lead-ink: #f4f0d8;
  }
  * { box-sizing: border-box; margin: 0; padding: 0; }
  html, body { width: 800px; height: 1200px; overflow: hidden; background: var(--page); }
  .canvas { position: relative; width: 800px; height: 1200px; }

  .label {
    position: absolute; left: 50px; top: 360px; width: 700px; height: 480px;
    overflow: hidden;
    background: linear-gradient(90deg, var(--gold-light) 0%, #d9c97f 22%, var(--gold-mid) 45%, var(--gold-deep) 55%, #c9b06a 75%, var(--gold-pale) 100%);
  }

  .brand {
    position: absolute; top: 22px; left: 0; width: 100%;
    display: flex; justify-content: center; align-items: center; gap: 8px;
  }
  .brand-mark { width: 14px; height: 14px; background: var(--brand-orange); }
  .brand-name {
    font-family: "Open Sans", sans-serif; font-weight: 600; font-size: 30px;
    color: var(--brand-orange); letter-spacing: 0.5px;
  }

  .foliage {
    position: absolute; inset: 110px 0 170px 0;
    background: radial-gradient(ellipse at 8% 55%, rgba(217,191,134,0.65), transparent 40%),
                radial-gradient(ellipse at 92% 45%, rgba(240,232,200,0.8), transparent 38%);
  }

  .swash {
    position: absolute; left: 60px; top: 150px; width: 560px; height: 80px;
  }

  .product-name {
    position: absolute; top: 92px; left: 0; width: 100%; text-align: center;
    font-family: "Great Vibes", cursive; font-size: 110px; line-height: 1;
    color: var(--script-green); font-weight: 400;
  }
  .origin {
    position: absolute; top: 226px; left: 0; width: 100%; text-align: center;
    font-family: "Dancing Script", cursive; font-weight: 500; font-size: 28px;
    color: var(--ink); padding-right: 60px;
  }

  .forest {
    position: absolute; left: 0; right: 0; bottom: 0; height: 205px;
    background: linear-gradient(180deg, var(--forest-light) 0%, var(--forest-mid) 45%, var(--forest-dark) 100%);
    clip-path: polygon(0 30%, 8% 22%, 16% 40%, 26% 8%, 36% 35%, 46% 14%, 56% 30%, 66% 6%, 76% 32%, 86% 12%, 94% 28%, 100% 18%, 100% 100%, 0 100%);
  }

  .best-before-lead {
    position: absolute; right: 18px; bottom: 64px;
    font-family: "Open Sans Condensed", "Open Sans", sans-serif; font-weight: 500;
    font-size: 20px; color: var(--lead-ink); white-space: nowrap;
  }
  .best-before {
    position: absolute; right: 18px; bottom: 22px;
    background: var(--tag-cream); padding: 3px 8px;
    font-family: "Open Sans Condensed", "Open Sans", sans-serif; font-weight: 500;
    font-size: 20px; color: var(--tag-ink); white-space: nowrap;
  }
</style>
</head>
<body>
<div class="canvas">
  <section class="label">
    <div class="foliage" role="img" aria-label="Herbstlaub, helle und goldene Ahornblätter"></div>

    <header class="brand">
      <span class="brand-mark"></span>
      <span class="brand-name">verdanta</span>
    </header>

    <svg class="swash" viewBox="0 0 560 80" aria-hidden="true">
      <path d="M10 8 C30 55, 110 68, 280 62 S500 50, 550 66" fill="none" stroke="var(--swash-green)" stroke-width="4" stroke-linecap="round"/>
    </svg>

    <h1 class="product-name">Waldhonig</h1>
    <p class="origin">aus dem Glottertal</p>

    <div class="forest" role="img" aria-label="Silhouette eines grünen Tannenwaldes"></div>

    <p class="best-before-lead">Mindestens haltbar bis</p>
    <p class="best-before">L 30. Okt. I Nov. I Dez. I 2022</p>
  </section>
</div>
</body>
</html>
```